Career-focused learning application platform

We have a K-12 learning application platform designed for grades 6-12 that needs user interface improvements that provide a positive experience for all users (teachers and students). The learning platform provides career-focused math curriculum and career exploration resources. We would like to improve the user-interface with engaging design elements without taking away from the functionality and performance of the platform.

```html
<!DOCTYPE html>
<html lang="en">
<head>
<meta charset="utf-8">
<title>CareerRoute – Sign In and Dashboard</title>
<link href="https://fonts.googleapis.com/css2?family=Roboto:wght@400;500;700&family=Saira+Semi+Condensed:wght@700;800&display=swap" rel="stylesheet">
<style>
  :root{
    --page:#e4e4e4;
    --white:#ffffff;
    --soft:#f6f6fb;
    --orange:#f7921e;
    --orange-deep:#8a4d12;
    --purple:#25124a;
    --ink:#1d1d1f;
    --text:#3c3c3c;
    --muted:#8a8a8a;
    --line:#d9d9d9;
    --slate:#535755;
    --cream:#fdf4e6;
    --ring:#dedad4;
  }
  *{box-sizing:border-box;margin:0;padding:0}
  html,body{width:1200px;height:2402px;overflow:hidden}
  body{background:var(--page);font-family:"Roboto",Arial,sans-serif;color:var(--ink);position:relative}
  .abs{position:absolute}
  .brand{position:absolute;font-family:"Roboto",Arial,sans-serif;font-weight:700;color:var(--orange);display:flex;align-items:center;gap:8px}
  .brand .dot{width:14px;height:14px;border-radius:50%;background:var(--orange)}

  /* Sign-in screen */
  .signin-screen{left:105px;top:112px;width:988px;height:640px;background:linear-gradient(135deg,#ffffff 0%,#f1f1f1 45%,#fafafa 60%,#ececec 100%);overflow:hidden}
  .signin-screen .brand{left:72px;top:40px;font-size:20px}
  .account-note{position:absolute;right:72px;top:37px;font-size:13.5px;color:#555}
  .account-note a{color:var(--purple);font-weight:500;text-decoration:none;margin-left:10px}
  .signin-card{position:absolute;left:322px;top:94px;width:347px;height:479px;background:var(--white);border-radius:4px;box-shadow:0 4px 18px rgba(0,0,0,.06);text-align:center}
  .signin-kicker{margin-top:33px;font-size:13px;font-weight:500;color:var(--purple)}
  .signin-title{margin-top:5px;font-size:20px;font-weight:700;color:var(--ink)}
  .title-rule{width:35px;height:2px;background:var(--orange);margin:12px auto 0}
  .field{position:absolute;left:31px;width:285px;height:42px;border:1px solid var(--line);border-radius:4px;font-size:11px;color:var(--muted);text-align:left;padding:14px 19px}
  .remember{position:absolute;left:51px;top:224px;display:flex;align-items:center;gap:8px;font-size:13px;color:var(--ink)}
  .check{width:16px;height:16px;border-radius:3px;background:var(--orange);display:flex;align-items:center;justify-content:center}
  .forgot{position:absolute;right:40px;top:225px;font-size:12.5px;color:var(--purple);font-weight:500}
  .signin-btn{position:absolute;left:31px;top:272px;width:285px;height:39px;border-radius:4px;background:var(--orange);color:#fff;font-size:13px;font-weight:500;line-height:39px}
  .or-row{position:absolute;left:45px;top:339px;width:255px;display:flex;align-items:center;gap:8px;font-size:11.5px;color:var(--muted)}
  .or-row span.rule{flex:1;height:1px;background:var(--line)}
  .create-note{position:absolute;left:0;right:0;top:366px;font-size:14px;color:var(--ink)}
  .provider{position:absolute;top:401px;width:89px;height:43px;border:1px solid var(--line);border-radius:4px;font-size:12px;color:#555;line-height:41px}

  /* Dashboard */
  .dashboard{left:105px;top:854px;width:988px;height:1436px;background:var(--soft)}
  .topbar{position:absolute;left:0;top:0;width:988px;height:70px;background:var(--white)}
  .topbar .brand{left:42px;top:24px;font-size:17px}
  .nav{position:absolute;top:27px;font-size:13px;color:var(--ink);display:flex;align-items:center;gap:6px}
  .nav svg{width:12px;height:12px;fill:#2a2a2a}
  .user{position:absolute;left:860px;top:19px;display:flex;align-items:center;gap:8px;font-size:12px;font-weight:500}
  .avatar{width:30px;height:30px;border-radius:50%;background:linear-gradient(#c9c9c9,#7d7d7d)}
  .section-title{position:absolute;left:42px;font-family:"Saira Semi Condensed",sans-serif;font-weight:800;font-size:27px;color:#2b2b2b;letter-spacing:.3px}

  .spotlight{position:absolute;left:44px;top:178px;width:902px;height:372px;background:var(--white);box-shadow:0 2px 10px rgba(0,0,0,.08)}
  .spotlight-band{position:absolute;left:0;top:0;width:431px;height:38px;background:linear-gradient(90deg,var(--orange-deep),var(--orange));clip-path:polygon(0 0,100% 0,93.5% 100%,0 100%);color:#fff;font-weight:700;font-size:19px;padding:7px 0 0 37px}
  .spotlight h3{position:absolute;left:38px;font-size:17px;font-weight:500;color:var(--ink)}
  .spotlight p{position:absolute;left:37px;top:95px;width:390px;font-size:12px;line-height:20.5px;color:#555}
  .earning{position:absolute;top:228px;width:114px;height:114px}
  .earning svg{position:absolute;left:0;top:0}
  .earning .label{position:absolute;left:0;right:0;top:40px;text-align:center;font-size:17px;font-weight:500;color:var(--ink);line-height:19px}
  .earning .amount{display:block;font-size:13px;color:var(--orange);font-weight:500}
  .video{position:absolute;left:469px;top:56px;width:396px;height:285px;background:linear-gradient(110deg,#e9ecef 0%,#b7bec6 35%,#6d7a86 55%,#d7b8a3 70%,#2f5a7c 100%);border-radius:4px}
  .play{position:absolute;left:194px;top:120px;width:40px;height:40px;border-radius:50%;background:var(--orange);display:flex;align-items:center;justify-content:center}

  .class-card{position:absolute;top:714px;width:275px;height:245px;border:3px solid var(--purple);border-top:none;border-radius:0 0 5px 5px;text-align:center}
  .class-card::before{content:"";position:absolute;left:-3px;right:-3px;top:0;height:3px;background:inherit}
  .class-card .frame-top{position:absolute;left:-3px;right:-3px;top:0;height:3px;background:var(--purple)}
  .class-card.featured{border-color:var(--orange)}
  .class-card.featured .frame-top{background:var(--orange)}
  .teacher-pill{position:absolute;left:14px;top:-20px;width:244px;height:43px;border-radius:22px;background:var(--purple);color:#fff;display:flex;align-items:center;padding-left:8px;gap:16px;font-size:14.5px;font-weight:500}
  .featured .teacher-pill{background:var(--orange)}
  .teacher-pill small{font-size:10px}
  .pill-icon{width:28px;height:28px;border-radius:50%;background:#fff;display:flex;align-items:center;justify-content:center}
  .class-cover{position:absolute;left:93px;top:52px;width:89px;height:87px;border-radius:3px}
  .class-name{position:absolute;left:0;right:0;top:163px;font-size:14px;font-weight:500;color:var(--ink)}
  .class-btn{position:absolute;left:87px;top:189px;width:101px;height:29px;border-radius:15px;background:var(--purple);color:#fff;font-size:13px;font-weight:500;line-height:29px}
  .featured .class-btn{background:var(--orange)}

  .subtitle{position:absolute;left:43px;top:1071px;font-size:14px;color:#444}
  .lessons{position:absolute;left:67px;top:1123px;width:856px}
  .lessons-head{position:relative;height:45px}
  .lessons-head div{position:absolute;top:0;height:45px;background:var(--slate);color:#fff;font-size:19px;font-weight:500;text-align:center;line-height:45px}
  .lessons-head div::after{content:"";position:absolute;left:50%;bottom:-11px;margin-left:-7px;border:7px solid transparent;border-top:6px solid var(--slate);border-bottom:0}
  .lessons-head div.hl{background:var(--orange)}
  .lessons-head div.hl::after{border-top-color:var(--orange)}
  .lesson-row{position:relative;height:48px;font-size:12.5px;color:#333;background:#fff}
  .lesson-row.first{height:65px}
  .lesson-row.alt{background:var(--cream)}
  .lesson-row span{position:absolute;bottom:15px;text-align:center}
  .c1{left:0;width:282px}.c2{left:287px;width:281px}.c3{left:575px;width:281px}
</style>
</head>
<body>

<section class="abs signin-screen" aria-label="Sign in screen">
  <div class="brand"><span class="dot"></span>CareerRoute</div>
  <div class="account-note">You do not have an account?<a href="#">Register</a></div>

  <form class="signin-card">
    <div class="signin-kicker">SIGN IN</div>
    <div class="signin-title">With Your School Account</div>
    <div class="title-rule"></div>
    <div class="field" style="top:116px">Email Address</div>
    <div class="field" style="top:169px">Password</div>
    <div class="remember">
      <span class="check"><svg width="10" height="8" viewBox="0 0 10 8"><path d="M1 4l3 3 5-6" stroke="#fff" stroke-width="1.8" fill="none"/></svg></span>
      Remember me
    </div>
    <div class="forgot">Forgot password?</div>
    <div class="signin-btn">SIGN IN</div>
    <div class="or-row"><span class="rule"></span>OR<span class="rule"></span></div>
    <div class="create-note">Create account using</div>
    <div class="provider" style="left:76px">Northline</div>
    <div class="provider" style="left:181px">Glider</div>
  </form>
</section>

<main class="abs dashboard">
  <header class="topbar">
    <div class="brand"><span class="dot"></span>CareerRoute</div>
    <div class="nav" style="left:302px"><svg viewBox="0 0 12 12"><path d="M6 1L0 6h2v5h3V8h2v3h3V6h2z"/></svg>Home</div>
    <div class="nav" style="left:383px"><svg viewBox="0 0 12 12"><path d="M4 2h4v2h4v7H0V4h4zm1 1v1h2V3z"/></svg>Career Tools</div>
    <div class="nav" style="left:502px"><svg viewBox="0 0 12 12"><path d="M3 1h8l-2 10H1z"/></svg>Classes</div>
    <div class="nav" style="left:593px"><svg viewBox="0 0 12 12"><path d="M2 0h6l3 3v9H2z"/></svg>Assessments</div>
    <div class="nav" style="left:716px"><svg viewBox="0 0 12 12"><circle cx="6" cy="6" r="4"/><circle cx="6" cy="6" r="1.6" fill="#fff"/></svg>Help</div>
    <svg class="abs" style="left:807px;top:27px" width="14" height="15" viewBox="0 0 14 15"><path d="M7 1a4 4 0 014 4v4l2 2H1l2-2V5a4 4 0 014-4zm-2 11h4a2 2 0 01-4 0z" fill="#f7921e"/></svg>
    <div class="user"><span class="avatar"></span>Sam Rivera <svg width="8" height="5" viewBox="0 0 8 5"><path d="M1 1l3 3 3-3" stroke="#333" fill="none"/></svg></div>
  </header>

  <h2 class="section-title" style="top:118px">CAREER SPOTLIGHT</h2>
  <article class="spotlight">
    <div class="spotlight-band">Plumbers, Pipefitters, &amp; Steamfitters</div>
    <h3 style="top:60px">What They do</h3>
    <p>Assemble, install, alter, and repair pipelines or pipe systems that carry water, steam, air, or other liquids or gases. May install heating and cooling equipment and mechanical control systems, Includes sprinkler fitters.</p>
    <h3 style="top:194px">Earnings</h3>

    <div class="earning" style="left:47px">
      <svg width="114" height="114" viewBox="0 0 114 114"><circle cx="57" cy="57" r="55" fill="none" stroke="var(--ring)" stroke-width="3"/><path d="M57 2A55 55 0 0 0 2 57" fill="none" stroke="var(--orange)" stroke-width="3"/></svg>
      <div class="label">Low End<span class="amount">$33,46</span></div>
    </div>
    <div class="earning" style="left:185px">
      <svg width="114" height="114" viewBox="0 0 114 114"><circle cx="57" cy="57" r="55" fill="none" stroke="var(--ring)" stroke-width="3"/><path d="M2 57A55 55 0 0 1 112 57" fill="none" stroke="var(--orange)" stroke-width="3"/></svg>
      <div class="label">Median<span class="amount">$56,330</span></div>
    </div>
    <div class="earning" style="left:324px">
      <svg width="114" height="114" viewBox="0 0 114 114"><circle cx="57" cy="57" r="55" fill="none" stroke="var(--ring)" stroke-width="3"/><path d="M2 57A55 55 0 1 1 30 105" fill="none" stroke="var(--orange)" stroke-width="3"/></svg>
      <div class="label">High End<span class="amount">$98,990</span></div>
    </div>

    <div class="video" role="img" aria-label="Video still of a plumber tightening a chrome sink drain pipe with a wrench">
      <div class="play"><svg width="14" height="16" viewBox="0 0 14 16"><path d="M2 1l11 7-11 7z" fill="#fff"/></svg></div>
    </div>
  </article>

  <h2 class="section-title" style="top:630px">CLASSES</h2>

  <div class="class-card" style="left:55px">
    <span class="frame-top"></span>
    <div class="teacher-pill"><span class="pill-icon"><svg width="16" height="16" viewBox="0 0 16 16"><circle cx="8" cy="5" r="3" fill="#25124a"/><path d="M2 15a6 5 0 0112 0z" fill="#25124a"/></svg></span><span>Math Teacher , <small>Period 1</small></span></div>
    <div class="class-cover" role="img" aria-label="Course cover for 8th grade math and pre-algebra" style="background:linear-gradient(#1c4a6e 0 45%,var(--orange) 45%)"></div>
    <div class="class-name">8th Grade Math / Pre-Algebra</div>
    <div class="class-btn">View Class</div>
  </div>

  <div class="class-card featured" style="left:357px">
    <span class="frame-top"></span>
    <div class="teacher-pill"><span class="pill-icon"><svg width="16" height="16" viewBox="0 0 16 16"><circle cx="8" cy="5" r="3" fill="#f7921e"/><path d="M2 15a6 5 0 0112 0z" fill="#f7921e"/></svg></span><span>Math Teacher , <small>Period 1</small></span></div>
    <div class="class-cover" role="img" aria-label="Course cover for algebra one" style="background:linear-gradient(#5b2448 0 45%,var(--orange) 45%)"></div>
    <div class="class-name">8th Grade Math / Pre-Algebra</div>
    <div class="class-btn">View Class</div>
  </div>

  <div class="class-card" style="left:660px">
    <span class="frame-top"></span>
    <div class="teacher-pill"><span class="pill-icon"><svg width="16" height="16" viewBox="0 0 16 16"><circle cx="8" cy="5" r="3" fill="#25124a"/><path d="M2 15a6 5 0 0112 0z" fill="#25124a"/></svg></span><span>Math Teacher , <small>Period 1</small></span></div>
    <div class="class-cover" role="img" aria-label="Course cover for algebra one" style="background:linear-gradient(#5b2448 0 45%,var(--orange) 45%)"></div>
    <div class="class-name">8th Grade Math / Pre-Algebra</div>
    <div class="class-btn">View Class</div>
  </div>

  <h2 class="section-title" style="top:1032px">UPCOMING LESSONS</h2>
  <div class="subtitle">Lessons due up to the next 7 Days:</div>

  <div class="lessons" role="table">
    <div class="lessons-head">
      <div class="c1">Class</div>
      <div class="c2 hl">Lesson</div>
      <div class="c3">Due</div>
    </div>
    <div class="lesson-row first"><span class="c1">Period 1</span><span class="c2">1.1 - Translations</span><span class="c3">October 15th at 11:59PM</span></div>
    <div class="lesson-row alt"><span class="c1">Period 1</span><span class="c2">2.1 - Operations With Rational Numbers</span><span class="c3">October 18th at 11:59PM</span></div>
    <div class="lesson-row"><span class="c1">Period 1</span><span class="c2">3.1 - Parallel Lines and Transversals</span><span class="c3">October 19th at 11:59PM</span></div>
    <div class="lesson-row alt"><span class="c1">Period 1</span><span class="c2">3.3 - Angle Relationships in Triangles</span><span class="c3">October 21th at 11:59PM</span></div>
  </div>
</main>

</body>
</html>
```